Stage Design Company Business Card

We are looking to step up up our business card design for our team.

We are a Full service Design and Consultation company for Stage and TV with an emphasis in Theatrical Lighting.

We like our materials to be clean and modern with solid colors free of patterns and gradients. Our brand consists of 4 primary colors Purple, Black, Grey, and White. Provided is our Word Mark as well as our Symbol Logo.

We would like our cards to leave an impression beyond the information, show our attention to design and detail, and make our marks an easily recognized feature (together or apart) for our clients.

We need a warm approachable comfortable feel for some clients, and a professional flair for the board member type clients.

Attached are our brand elements, and our existing cards to give a sense of our style and a glipse at the information we provide on our cards.

Target Market(s)

broad client base from church leaders to high school teachers and architects.

Industry/Entity Type

Business

Contact Information for Business Card

We format our phone number with periods not parenthesis or dashes. Information will be edited for each of our team members, and team member specific cards are not part of this scope, but rather a template so to speak.

Font styles to use
Sans Serif

Colors
6b449b
ffffff
000000
333333
aaaaaa

Requirements
Must have
• Wordmark and logo mark present (does not need to exist on the same side of card)
• Brand Colors,
• Name, Phone, Email, Address.
• Unique choices that make someone stop and take a second look
Nice to have
• It would be nice to somehow convey what we DO, as our brand name does not lend itself to this, outside of an obvious tagline though.....
• social media if not crowded. all of our handles match (instagram, twitter, facebook)
Should not have
• "clipart"

```html
<!DOCTYPE html>
<html lang="en">
<head>
<meta charset="utf-8">
<title>Marlow Stageworks Business Card</title>
<link rel="stylesheet" href="https://fonts.googleapis.com/css2?family=Questrial&display=swap">
<style>
  :root {
    --backdrop: #5e5e5e;
    --brand-purple: #3a2870;
    --accent-purple: #4a2a8a;
    --ink: #1c1c1c;
    --grey: #555555;
    --light-grey: #aaaaaa;
    --white: #ffffff;
  }
  * { margin: 0; padding: 0; box-sizing: border-box; }
  html, body {
    width: 1200px; height: 1200px; overflow: hidden;
    background: var(--backdrop);
    font-family: "Questrial", sans-serif;
  }
  .canvas { position: relative; width: 1200px; height: 1200px; }
  .card {
    position: absolute; top: 156px; width: 520px; height: 887px;
    text-align: center;
  }
  .card--front { left: 60px; background: var(--white); color: var(--ink); }
  .card--back { left: 620px; background: var(--brand-purple); color: var(--white); }
  .card > * { position: absolute; left: 0; width: 100%; }

  .brand-dot {
    left: 50%; width: 150px; height: 150px; margin-left: -75px; top: 100px;
    border-radius: 50%; background: var(--accent-purple);
  }
  .brand-name { top: 330px; font-size: 50px; letter-spacing: 30px; padding-left: 30px; line-height: 1; }
  .brand-sub { top: 408px; font-size: 14px; letter-spacing: 16px; padding-left: 16px; line-height: 1; }
  .card--back .brand-name { top: 398px; color: var(--white); }
  .card--back .brand-sub { top: 470px; color: var(--white); }

  .person-name { top: 482px; font-size: 38px; color: var(--accent-purple); line-height: 1; }
  .person-title { top: 532px; font-size: 21px; color: var(--grey); line-height: 1; }
  .contact { top: 590px; font-size: 25px; color: var(--grey); line-height: 33px; }
  .contact-line { display: flex; justify-content: center; align-items: center; gap: 10px; }
  .contact-line svg { width: 22px; height: 22px; stroke: var(--accent-purple); fill: none; stroke-width: 1.6; }
  .address { top: 688px; font-size: 25px; color: var(--grey); line-height: 32px; }
  .website { top: 808px; font-size: 32px; letter-spacing: 14px; padding-left: 14px; color: var(--accent-purple); line-height: 1; }

  .social-handle { top: 784px; font-size: 25px; color: var(--light-grey); line-height: 1; }
</style>
</head>
<body>
<main class="canvas">
  <section class="card card--front" aria-label="Card front">
    <div class="brand-dot" aria-hidden="true"></div>
    <div class="brand-name">MARLOW</div>
    <div class="brand-sub">STAGEWORKS</div>
    <div class="person-name">Evan R Holt</div>
    <div class="person-title">JOB TITLE</div>
    <div class="contact">
      <div class="contact-line">
        <svg viewBox="0 0 24 24" aria-hidden="true"><path d="M6 3l3 4-2 2c1 3 4 6 7 7l2-2 4 3-2 3C10 20 4 14 3 5z"/></svg>
        <span>555.014.2270</span>
      </div>
      <div class="contact-line">
        <svg viewBox="0 0 24 24" aria-hidden="true"><rect x="3" y="6" width="18" height="12"/><path d="M3 6l9 7 9-7"/></svg>
        <span>evan@marlow-s.com</span>
      </div>
    </div>
    <div class="address">18 N Elm St<br>Cedar Vale, AZ 85010</div>
    <div class="website">MARLOW-S.COM</div>
  </section>

  <section class="card card--back" aria-label="Card back">
    <div class="brand-name">MARLOW</div>
    <div class="brand-sub">STAGEWORKS</div>
    <div class="social-handle">@marlowstage</div>
  </section>
</main>
</body>
</html>
```